Exclusive beauty salon needs a price list or services booklet

I need a new very attractive flyer for my beauty salon, containing information on the different services and their prices.
In attachment you can find a pdf of the "old" one, but I'd love to have a beautifully designed new one!
I'd love to have a booklet in format 148 x 148 mm, or in US format, containing 12 or 16 pages, but if you can offer other nice looking designs they are welcome!
The services that need to come in the booklet with their prices can all be found on my website: www.atelierverano.be, starting with
Gelaatsverzorging
Wimperverlenging
Suikerontharing
Wimperlifting
Permanente Make Up
Airbrush Tanning

Target Market(s)

woman from 20 to 89 years old

Industry/Entity Type

Beauty Salon

Font styles to use
Sans Serif

Colors

Designer to choose colors to be used in the design.

Requirements
Must have
• a classy nice look, it must contain details about the services from my beauty salon and their prices, and nice pictures.
• The Names, prices and explanations of the services can easily be found on my website: www.atelierverano.be
Nice to have
• In attachment you can find the "old" price list in pdf, what I need now is a "new booklet" with the new logo and updated services price list.
• I need a very nice and attractive looking booklet, classy chique, Paris chique, looking very expensive.
Should not have
• Not too much colors, not too curly, but still feminine

```html
<!DOCTYPE html>
<html lang="nl">
<head>
<meta charset="utf-8">
<title>Atelier Verano – Prijsboekje</title>
<link rel="stylesheet" href="https://fonts.googleapis.com/css2?family=Open+Sans:ital,wght@0,300;0,400;0,600;1,300;1,400&family=Raleway:wght@300&display=swap">
<style>
:root{
  --backdrop:#5e5e60;
  --paper:#ffffff;
  --panel:#a7a7a9;
  --teal:#7ecfd4;
  --teal-deep:#4fb8be;
  --ink:#6b6b6d;
  --ink-soft:#8d8d90;
}
*{box-sizing:border-box;margin:0;padding:0}
html,body{width:1200px;height:3137px;overflow:hidden}
body{background:var(--backdrop);font-family:"Open Sans",Arial,sans-serif;color:var(--ink);position:relative}
.booklet{position:absolute;left:98px;top:95px;display:grid;grid-template-columns:476px 476px;column-gap:52px;row-gap:22px;grid-auto-rows:350px}
.page{position:relative;background:var(--paper);overflow:hidden;box-shadow:0 2px 6px rgba(0,0,0,.35)}
.page--framed{background:var(--panel);padding:14px}
.page--framed .inner{position:relative;background:var(--paper);width:100%;height:100%;overflow:hidden}
.page--grey{background:var(--paper);padding:14px}
.page--grey .inner{position:relative;background:var(--panel);width:100%;height:100%;overflow:hidden}
.photo{position:absolute}
.photo--skin{background:linear-gradient(135deg,#f3e3d8,#e2bea8 60%,#c9a08a)}
.photo--studio{background:linear-gradient(135deg,#d9dde2,#e8cfc2 50%,#b9a89f)}
.photo--wax{background:linear-gradient(120deg,#f4e8dd,#e3b98d 45%,#c97c2e 70%,#f1e2d4)}
.photo--lash{background:linear-gradient(135deg,#f1d3c7,#e9b8a8 55%,#fdfbf9)}
.photo--tan{background:linear-gradient(160deg,#fbf6f2,#d8a47e 55%,#8a5a3c)}
.body-copy{font-size:7px;line-height:1.5;font-style:italic;color:var(--ink)}
.body-copy p+p{margin-top:5px}
.heading{font-size:11px;color:var(--teal-deep);font-weight:400;margin:6px 0 3px}
.heading:first-child{margin-top:0}
.price-line{font-size:7px;color:var(--teal-deep);text-align:right;margin-top:2px}
.bullets{list-style:none;font-size:7px;font-style:italic;line-height:1.5}
.bullets li{padding-left:9px;position:relative}
.bullets li::before{content:"";position:absolute;left:0;top:5px;width:3px;height:3px;background:var(--ink-soft);border-radius:50%}
.rates{font-size:7.5px;font-style:italic;width:100%}
.rates-title{font-size:10px;color:var(--teal-deep);margin-bottom:4px}
.rates .row{display:flex;justify-content:space-between;border-bottom:1px solid #e2e2e2;padding:1.5px 0}
.rates .row span:last-child{color:var(--teal-deep)}
.teal-box{position:absolute;background:var(--teal);color:#fff;font-weight:300}
.brand-name{font-family:"Raleway",sans-serif;font-weight:300;letter-spacing:.35em;color:#4a4a4c;white-space:nowrap}
.white-copy{color:#fff}
</style>
</head>
<body>
<main class="booklet">

  <section class="page">
    <div style="position:absolute;left:22px;top:22px;right:22px;height:210px;background:var(--teal)"></div>
    <div style="position:absolute;left:70px;top:94px;width:330px;height:76px;background:#fff;display:flex;align-items:center">
      <div style="width:160px;text-align:center;border-right:1px solid #ddd">
        <div class="brand-name" style="font-size:11px;letter-spacing:.2em">ATELIER VERANO</div>
        <div style="font-size:5px;letter-spacing:.2em;color:var(--ink-soft);margin-top:3px">SCHOONHEIDSINSTITUUT</div>
      </div>
      <div style="padding-left:14px;font-size:6px;line-height:1.6;color:var(--ink-soft)">
        Atelier Verano Schoonheidsinstituut<br>Lindenlaan 14, 2000 Voorstad<br>03 555 01 27<br>0470 55 18 64<br>info@atelierverano.be<br>www.atelierverano.be
      </div>
    </div>
  </section>

  <section class="page">
    <div style="position:absolute;left:0;right:0;top:128px;text-align:center">
      <div class="brand-name" style="font-size:30px">ATELIER VERANO</div>
      <div style="font-size:7px;letter-spacing:.45em;color:var(--ink-soft);margin-top:8px">SCHOONHEIDSINSTITUUT</div>
    </div>
    <div style="position:absolute;right:14px;bottom:26px;font-size:6px;color:var(--ink-soft)">www.atelierverano.be</div>
    <div style="position:absolute;right:14px;bottom:18px;width:80px;height:3px;background:var(--teal)"></div>
  </section>

  <section class="page page--grey">
    <div class="inner">
      <div style="position:absolute;left:116px;top:82px;width:220px;height:160px;border:1px solid #fff;padding:12px 14px" class="body-copy white-copy">
        <p>Al meer dan 5 jaar zorg ik met veel passie en aandacht voor elke klant, om mijn klanten met een glimlach te ontvangen. Mijn specialiteiten zijn gelaatsverzorgingen met de kwaliteitsvolle producten van Maison Alba, wimperextensions, suikerontharing en Permanente Make Up.</p>
        <p>Ik volg regelmatig bijscholingen om bij te blijven met de nieuwste trends.</p>
        <p>Eline Verhoeven, uw Schoonheidsspecialiste</p>
      </div>
    </div>
  </section>

  <section class="page">
    <div style="position:absolute;left:12px;top:12px;right:12px;bottom:12px;border:1px solid #ccc"></div>
    <div class="photo photo--skin" role="img" aria-label="Portretfoto van de schoonheidsspecialiste" style="left:14px;top:14px;width:300px;bottom:14px;background:linear-gradient(90deg,#fff,#f1e4da 30%,#e1c2ad 55%,#fff)"></div>
    <div class="brand-name" style="position:absolute;right:30px;top:30px;font-size:7px;letter-spacing:.2em">ATELIER VERANO</div>
    <div class="teal-box" style="left:340px;top:140px;width:100px;height:126px;padding:10px 12px;font-size:20px;line-height:1.15">Steeds tot uw dienst</div>
  </section>

  <section class="page page--framed">
    <div class="inner">
      <div class="photo photo--studio" role="img" aria-label="Foto van een behandeling permanente make-up" style="left:0;top:0;width:210px;bottom:0"></div>
      <div style="position:absolute;left:222px;top:10px;right:12px" class="body-copy">
        <div class="heading">Permanente Make Up</div>
        <p>Permanente make-up is een semi-permanente techniek waarbij pigment in de bovenste huidlaag wordt aangebracht. Zo blijven wenkbrauwen, eyeliner of lippen mooi gedefinieerd, elke dag opnieuw, zonder gedoe.</p>
        <p>Het resultaat is subtiel en natuurlijk, aangepast aan uw gelaat, huidtype en persoonlijke wensen. Na enkele weken volgt een bijwerking voor een perfect eindresultaat.</p>
        <p>Wij werken uitsluitend met veilige pigmenten en steriel materiaal. Uw comfort en veiligheid staan altijd voorop.</p>
      </div>
      <div class="teal-box" style="left:222px;top:216px;right:12px;height:80px;padding:7px 9px">
        <div style="font-size:9px;margin-bottom:3px">GRATIS ADVIESGESPREK</div>
        <div style="font-size:6.5px;font-style:italic;line-height:1.5">Voor elke behandeling plannen we een vrijblijvend gesprek. Samen bekijken we de vorm, de kleur en het gewenste resultaat, zodat u met een gerust gevoel kunt beslissen.</div>
      </div>
    </div>
  </section>

  <section class="page page--framed">
    <div class="inner">
      <div style="position:absolute;left:14px;top:10px;width:220px">
        <div class="heading" style="font-size:9px">Wanneer is Permanente Make-Up Zinvol?</div>
        <ul class="bullets">
          <li>U heeft een lichte of dunne wenkbrauwlijn</li>
          <li>U wilt elke ochtend tijd besparen</li>
          <li>U sport veel of zwemt regelmatig</li>
          <li>U draagt een bril of lenzen</li>
          <li>U heeft last van allergie voor make-up</li>
          <li>U wilt een frisse en verzorgde uitstraling</li>
          <li>U heeft een onrustige of trillende hand</li>
        </ul>
        <div class="rates" style="margin-top:14px">
          <div class="rates-title">TARIEVEN</div>
          <div class="row"><span>Fijne eyeliner boven of onder</span><span>€180</span></div>
          <div class="row"><span>Brede eyeliner boven of onder</span><span>€220</span></div>
          <div class="row"><span>Volledige wenkbrauw</span><span>€320</span></div>
          <div class="row"><span>Wenkbrauw haartjes</span><span>€320</span></div>
          <div class="row"><span>Full Lips</span><span>€460</span></div>
        </div>
      </div>
      <div class="photo photo--skin" role="img" aria-label="Close-up foto van oog en lippen met permanente make-up" style="right:0;top:0;width:200px;bottom:0"></div>
    </div>
  </section>

  <section class="page page--framed">
    <div class="inner">
      <div class="photo photo--skin" role="img" aria-label="Foto van een vrouw met stralende huid" style="left:0;top:0;width:210px;bottom:0"></div>
      <div style="position:absolute;left:16px;bottom:12px;font-size:11px;letter-spacing:.25em;color:#4a4a4c">MAISON ALBA</div>
      <div style="position:absolute;left:222px;top:10px;right:12px" class="body-copy">
        <div class="heading">Gelaatsverzorging Maison Alba</div>
        <p>Elke huid is uniek. Daarom stemmen we elke verzorging af op uw huidtype en noden, met zachte technieken en verfijnde producten.</p>
        <div class="heading">Cosmetische Verzorging</div>
        <p>Reiniging, peeling, stomen, onzuiverheden verwijderen, masker en dagcrème.</p>
        <div class="price-line">€50</div>
        <div class="heading">Verwijderen van gerstekorrels</div>
        <p>Per behandeling of per stuk.</p>
        <div class="price-line">vanaf €17</div>
        <div class="heading">Snelle Reiniging</div>
        <p>Een snelle reiniging voor een frisse en stralende huid, ideaal voor een druk leven.</p>
        <div class="price-line">€29 – 30 min</div>
      </div>
    </div>
  </section>

  <section class="page page--framed">
    <div class="inner">
      <div style="position:absolute;left:14px;top:10px;width:230px" class="body-copy">
        <div class="heading">Hydraterende Verzorging</div>
        <p>Een diep hydraterende verzorging die de huid voedt en herstelt. Inclusief reiniging, peeling, massage, masker en dagverzorging.</p>
        <div class="price-line">€65 – 60 min</div>
        <div class="heading">Zuiverende Verzorging</div>
        <p>Een zuiverende behandeling voor de gemengde tot vette huid, met extra aandacht voor onzuiverheden en glans.</p>
        <div class="price-line">€65 – 60 min</div>
        <div class="heading">Luxe Verzorging Prestige</div>
        <p>Onze meest complete verzorging met lifting-effect, gelaatsmassage, serum en masker voor een stralende, uitgeruste huid.</p>
        <div class="price-line">€85 – 90 min</div>
      </div>
      <div class="photo photo--skin" role="img" aria-label="Foto van een vrouw met verzorgde huid" style="right:0;top:0;width:200px;bottom:0"></div>
    </div>
  </section>

  <section class="page page--framed">
    <div class="inner">
      <div class="photo photo--wax" role="img" aria-label="Foto van suikerontharing op een been" style="left:0;top:0;width:210px;bottom:0"></div>
      <div style="position:absolute;left:222px;top:10px;right:12px" class="body-copy">
        <div class="heading">Ontharing Met Suiker</div>
        <p>Suikerontharing is een eeuwenoude, natuurlijke methode. De pasta bestaat uit suiker, water en citroen en is zacht voor de huid.</p>
        <ul class="bullets" style="margin-top:5px">
          <li>Minder pijnlijk dan klassieke wax</li>
          <li>Geschikt voor de gevoelige huid</li>
          <li>Geen risico op verbranding</li>
          <li>Haartjes worden in groeirichting verwijderd</li>
          <li>Minder ingegroeide haren</li>
          <li>Langdurig resultaat tot vier weken</li>
          <li>Haargroei wordt op termijn fijner</li>
          <li>Volledig natuurlijk en hygiënisch</li>
          <li>Ook geschikt voor kortere haartjes</li>
        </ul>
      </div>
    </div>
  </section>

  <section class="page page--framed">
    <div class="inner">
      <div style="position:absolute;left:14px;top:10px;width:210px">
        <div class="rates">
          <div class="rates-title">TARIEVEN</div>
          <div class="row"><span>Wenkbrauwen</span><span>€9</span></div>
          <div class="row"><span>Wenkbrauwen vormgeven</span><span>€14</span></div>
          <div class="row"><span>Bovenlip of kin</span><span>€9</span></div>
          <div class="row"><span>Bovenlip en kin</span><span>€16</span></div>
          <div class="row"><span>Gezicht volledig</span><span>€26</span></div>
          <div class="row"><span>Oksels</span><span>€12</span></div>
          <div class="row"><span>Armen</span><span>€20</span></div>
          <div class="row"><span>Bikinilijn klassiek</span><span>€20</span></div>
          <div class="row"><span>Bikinilijn</span><span>€15</span></div>
          <div class="row"><span>Onderbenen</span><span>€26</span></div>
          <div class="row"><span>Bovenbenen</span><span>€30</span></div>
          <div class="row"><span>Volledige benen</span><span>€52</span></div>
          <div class="row"><span>Volledige benen + bikini</span><span>€65</span></div>
        </div>
      </div>
      <div style="position:absolute;left:14px;width:210px;bottom:22px;text-align:center">
        <div class="brand-name" style="font-size:9px;letter-spacing:.25em">ATELIER VERANO</div>
        <div style="font-size:4.5px;letter-spacing:.3em;color:var(--ink-soft);margin-top:2px">SCHOONHEIDSINSTITUUT</div>
      </div>
      <div class="photo photo--wax" role="img" aria-label="Foto van een pot suikerpasta met spatel" style="right:0;top:0;width:200px;bottom:0;background:linear-gradient(180deg,#f7efe7,#e8b57a 45%,#f4f4f2)"></div>
    </div>
  </section>

  <section class="page page--grey">
    <div class="inner">
      <div style="position:absolute;left:22px;top:28px;width:195px;height:200px;border:1px solid #fff;padding:8px" class="body-copy white-copy">
        <p>Lange, volle en gekrulde wimpers zonder mascara. Met wimperextensions wordt elke natuurlijke wimper afzonderlijk verlengd, voor een open en stralende blik.</p>
        <p>De extensions zijn licht, soepel en waterbestendig. U kunt gewoon sporten, zwemmen en douchen.</p>
        <p>Na een plaatsing blijven de wimpers enkele weken mooi. Een bijwerking houdt het resultaat vol en verzorgd.</p>
      </div>
      <div style="position:absolute;left:232px;top:28px;width:200px;height:200px;border:1px solid #fff;padding:8px" class="white-copy">
        <div style="font-size:7px;font-style:italic;margin-bottom:4px">Voordelen van Lash Atelier wimperverlenging:</div>
        <ul class="bullets" style="color:#fff">
          <li>Flexibele behandeling</li>
          <li>Geen beschadiging van de eigen wimper</li>
          <li>Onmiddellijk een verzorgde look</li>
          <li>Lange houdbaarheid</li>
          <li>Veilige lijm en steriele werkwijze</li>
          <li>Waterbestendig bij sporten en zwemmen</li>
          <li>Natuurlijk of volumineus resultaat</li>
          <li>Afgestemd op uw oogvorm</li>
          <li>Geen mascara meer nodig</li>
        </ul>
      </div>
      <div style="position:absolute;left:0;right:0;top:258px;text-align:center;color:#fff;font-size:9px;line-height:1.6">
        Eerste plaatsing wimperextensions €65<br>Bijwerking na max. 4 weken €35
      </div>
    </div>
  </section>

  <section class="page">
    <div class="photo photo--lash" role="img" aria-label="Close-up foto van het plaatsen van wimperextensions" style="left:14px;top:14px;right:14px;bottom:14px"></div>
    <div class="teal-box" style="left:40px;top:232px;width:158px;height:62px;padding:10px;font-size:11px;line-height:1.35;opacity:.92">Individuele Wimperverlenging Lash Atelier</div>
  </section>

  <section class="page">
    <div class="photo photo--lash" role="img" aria-label="Foto van wimpers vóór de wimperlifting, zijaanzicht" style="left:14px;top:14px;width:200px;height:150px"></div>
    <div class="photo photo--lash" role="img" aria-label="Foto van wimpers na de wimperlifting, zijaanzicht" style="left:262px;top:14px;width:200px;height:150px"></div>
    <div class="photo photo--lash" role="img" aria-label="Foto van een oog vóór de wimperlifting" style="left:14px;top:186px;width:200px;height:150px;background:linear-gradient(135deg,#f4e6dd,#d9c2b6 55%,#f6efea)"></div>
    <div class="photo photo--lash" role="img" aria-label="Foto van een oog na de wimperlifting" style="left:262px;top:186px;width:200px;height:150px;background:linear-gradient(135deg,#f4e6dd,#c8b4ad 55%,#f6efea)"></div>
    <svg style="position:absolute;left:230px;top:80px" width="12" height="14" viewBox="0 0 12 14"><path d="M1 1 L11 7 L1 13 Z" fill="#4a4a4c"/></svg>
    <svg style="position:absolute;left:230px;top:252px" width="12" height="14" viewBox="0 0 12 14"><path d="M1 1 L11 7 L1 13 Z" fill="#4a4a4c"/></svg>
    <div class="teal-box" style="left:180px;top:150px;width:110px;height:50px;padding:8px;font-size:11px;line-height:1.35;text-align:center;opacity:.92">Wimperlifting Lift Lashes</div>
  </section>

  <section class="page page--grey">
    <div class="inner">
      <div style="position:absolute;left:80px;top:56px;width:290px;border:1px solid #fff;padding:12px" class="body-copy white-copy">
        <p>Het hebben van mooie, lange en volumineuze wimpers staat hoog op het verlanglijstje van veel vrouwen. Het liefst heeft men de wimpers mooi gekruld voor een open blik.</p>
        <p>De nieuwe en revolutionaire methode zorgt ervoor dat uw eigen wimpers na één behandeling tot acht weken mooi gekruld blijven. Geen krultang of extensions meer nodig.</p>
      </div>
      <div style="position:absolute;left:0;right:0;top:228px;text-align:center;color:#fff;font-size:9px">Wimperlifting €65</div>
    </div>
  </section>

  <section class="page page--framed">
    <div class="inner">
      <div class="photo photo--tan" role="img" aria-label="Foto van een gebruinde huid na airbrush tanning" style="left:0;top:0;width:210px;bottom:0"></div>
      <div style="position:absolute;left:222px;top:10px;right:12px" class="body-copy">
        <div class="heading">Airbrush Tanning</div>
        <p>Altijd een gebruinde huid zonder zon of zonnebank. Met airbrush tanning krijgt u in korte tijd een egale, natuurlijke kleur die tot een week blijft.</p>
        <div class="heading">De Airbrush Tanning Zelf</div>
        <p>De bruiningslotion wordt met een fijne nevel aangebracht. De kleur ontwikkelt zich in enkele uren en past zich aan uw huidtint aan.</p>
        <p>Wij adviseren om vooraf een scrub te doen en de huid niet in te smeren. Draag na de behandeling losse, donkere kleding.</p>
      </div>
      <div style="position:absolute;left:222px;right:12px;bottom:14px;display:flex;justify-content:space-between;font-size:7px;font-style:italic">
        <span>Airbrush tanning van het volledige lichaam</span><span style="color:var(--teal-deep)">€39</span>
      </div>
    </div>
  </section>

  <section class="page page--grey">
    <div class="inner">
      <div style="position:absolute;left:110px;top:48px;width:230px;border:1px solid #fff;padding:10px" class="white-copy">
        <p class="body-copy white-copy">Atelier Verano Schoonheidsinstituut is gevestigd op de nieuwste verdieping van het winkelcentrum in Voorstad, met ruime parking.</p>
        <div style="font-size:7px;font-style:italic;margin:6px 0 3px">Voordelen van Atelier Verano:</div>
        <ul class="bullets" style="color:#fff">
          <li>Ruime openingsuren, ook op zaterdag</li>
          <li>Persoonlijk advies bij elke behandeling</li>
          <li>Verfijnde producten van hoge kwaliteit</li>
          <li>Gratis adviesgesprek voor elke nieuwe klant</li>
          <li>Rustige en stijlvolle behandelruimte</li>
          <li>Cadeaubonnen voor elke gelegenheid</li>
        </ul>
      </div>
    </div>
  </section>

</main>
</body>
</html>
```